BUSINESS CARD - HALLORAN FIELD SERVICES

I would like to create a business card for my fertilizer spreading business. I would like to incorporate my existing logo and also a description of the services offered. The business card will be given to farmers so must be kept simple but effective. It will also be left in stores so much also be eye catching in order to stand out from other cards.

Target Market(s)

FARMERS

Requirements
Must have
• FRONT OF CARD = EXISTING LOGO + "CUSTOMISED SPREADING" below the logo

REAR Of CARD = SERVICES OFFERED AND CONTACT DETAILS

- Bulk fertilizer including Lime, Gypsum, Manure & Compost
- Granular fertilizer including Single Super, Urea, Gran-am, & Custom Blends
- Modern equipment - Autosteer & Variable Rate Capable
- Friendly & Reliable Service
- Contact Gus: 0417 552 308
Nice to have
• utilize same color scheme as existing logo

```html
<!DOCTYPE html>
<html lang="en">
<head>
<meta charset="utf-8">
<title>Halloran Field Services – Business Card</title>
<link rel="stylesheet" href="https://fonts.googleapis.com/css2?family=Mulish:wght@400;600;700&display=swap">
<style>
  :root {
    --page-bg: #e4e4e4;
    --card-white: #ffffff;
    --ink-dark: #4a4a4c;
    --ink-mid: #5f5f62;
    --brand-grey: #6b6b6e;
    --brand-orange: #f4931f;
    --rear-top: #565658;
    --rear-bottom: #48484a;
    --rear-text: #f2f2f2;
  }
  * { box-sizing: border-box; margin: 0; padding: 0; }
  html, body {
    width: 1200px; height: 1200px; overflow: hidden;
    background: var(--page-bg);
    font-family: "Mulish", Arial, sans-serif;
  }
  .card {
    position: absolute; left: 257px;
    width: 686px; height: 392px;
    overflow: hidden;
  }
  /* Front */
  .card--front { top: 165px; background: var(--card-white); }
  .brand {
    position: absolute; right: 43px; top: 40px;
    display: flex; flex-direction: column; align-items: center;
    width: 200px;
  }
  .brand__dot {
    width: 86px; height: 86px; border-radius: 50%;
    background: var(--brand-grey);
  }
  .brand__name {
    margin-top: 10px;
    font-size: 19px; font-weight: 700; color: var(--brand-grey);
    white-space: nowrap; letter-spacing: 0.2px;
  }
  .brand__tagline {
    margin-top: 6px;
    font-size: 13px; font-weight: 400; color: var(--ink-mid);
    letter-spacing: 1.6px; white-space: nowrap;
  }
  .person { position: absolute; left: 41px; top: 254px; }
  .person__name { font-size: 21px; font-weight: 700; color: var(--ink-dark); letter-spacing: -0.3px; }
  .person__role { margin-top: 2px; font-size: 14.5px; color: var(--brand-orange); letter-spacing: 0.3px; }
  .divider {
    position: absolute; left: 41px; right: 41px; top: 309px;
    height: 1px; background: var(--ink-dark);
  }
  .contact {
    position: absolute; left: 41px; top: 323px;
    list-style: none; font-size: 15px; color: var(--ink-dark);
  }
  .contact li { display: flex; align-items: center; height: 20px; }
  .contact svg { width: 13px; height: 13px; margin-right: 9px; fill: var(--ink-dark); }
  .website {
    position: absolute; right: 44px; top: 343px;
    font-size: 15px; color: var(--ink-dark);
  }
  .edge-band {
    position: absolute; left: 0; bottom: 0; width: 100%; height: 11px;
  }
  /* Rear */
  .card--rear {
    top: 653px;
    background: linear-gradient(180deg, var(--rear-top), var(--rear-bottom));
  }
  .rear-mark {
    position: absolute; left: 0; right: 0; top: 62px;
    display: flex; flex-direction: column; align-items: center;
  }
  .rear-mark__dot {
    width: 180px; height: 180px; border-radius: 50%;
    background: radial-gradient(circle at 35% 30%, #6a6a6d, #333335);
  }
  .services {
    position: absolute; left: 0; right: 0; top: 288px;
    list-style: none; text-align: center;
    font-size: 15px; line-height: 19.5px; color: var(--rear-text);
  }
</style>
</head>
<body>
  <section class="card card--front" aria-label="Card front">
    <div class="brand">
      <div class="brand__dot" aria-hidden="true"></div>
      <div class="brand__name">Halloran Field Services</div>
      <div class="brand__tagline">CUSTOMISED SPREADING</div>
    </div>

    <div class="person">
      <div class="person__name">Gus Halloran</div>
      <div class="person__role">President</div>
    </div>
    <div class="divider"></div>

    <ul class="contact">
      <li>
        <svg viewBox="0 0 24 24" aria-hidden="true"><path d="M6.6 10.8a15.1 15.1 0 0 0 6.6 6.6l2.2-2.2c.3-.3.7-.4 1-.2 1.1.4 2.3.6 3.6.6.6 0 1 .4 1 1V20c0 .6-.4 1-1 1A17 17 0 0 1 3 4c0-.6.4-1 1-1h3.5c.6 0 1 .4 1 1 0 1.3.2 2.5.6 3.6.1.3 0 .7-.2 1z"/></svg>
        0417 552 308
      </li>
      <li>
        <svg viewBox="0 0 24 24" aria-hidden="true"><path d="M2 5h20v14H2z M4 7v.5l8 5 8-5V7z" fill-rule="evenodd"/></svg>
        info@halloranfield.com
      </li>
    </ul>
    <div class="website">www.halloranfield.com</div>

    <svg class="edge-band" viewBox="0 0 686 11" preserveAspectRatio="none" aria-hidden="true">
      <polygon points="0,0 434,0 430,11 0,11" fill="#4a4a4c"/>
      <polygon points="434,0 437,0 433,11 430,11" fill="#ffffff"/>
      <polygon points="437,0 686,0 686,11 433,11" fill="#f4931f"/>
    </svg>
  </section>

  <section class="card card--rear" aria-label="Card back">
    <div class="rear-mark">
      <div class="rear-mark__dot" aria-hidden="true"></div>
    </div>
    <ul class="services">
      <li>Bulk fertilizer including Lime, Gypsum, Manure &amp; Compost</li>
      <li>Granular fertilizer including Single Super, Urea, Gran-am, &amp; Custom Blends</li>
      <li>Modern equipment - Autosteer &amp; Variable Rate Capable</li>
      <li>Friendly &amp; Reliable Service</li>
    </ul>
  </section>
</body>
</html>
```